Help our Sugar Loom find our winning design! We're looking for a business card....

We’re a Sugar Loom in NY specializing in custom-made cakes and unique desserts.
Our cakes combine flavor and art, each designed to match customer’s special event and theme.
We’d like a unique business card with a clean design that will combine French chic and artistic look & feel.
We’d like to differentiate ourselves from standard bakeries, please don’t offer cupcake images :-)
Our logo is peach-pink and brown and we’d love to use these colors ( . Another color that can be added is gold - or feel free to suggest!

Target Market(s)

Women, ages 25-55

Industry/Entity Type

Boutique

Contact Information for Business Card

Text on card:
Logo
Sugar Loom by Dana Welch

www.sugarloomsweets.com
hello@sugarloom.com
(516) 555-0147
F – sugarloomnyc
IG - sugarloom_ny

Font styles to use
Sans Serif
Script

Requirements
Must have
• Logo
• Clean look
• French chic and artistic look & feel.
Nice to have
• Damask pattern
Should not have
• Cupcake images

```html
<!DOCTYPE html>
<html lang="en">
<head>
<meta charset="utf-8">
<title>Sugar Loom – Business Card</title>
<link rel="stylesheet" href="https://fonts.googleapis.com/css2?family=Great+Vibes&family=Open+Sans:wght@400;600&display=swap">
<style>
  :root {
    --backdrop: #d9d9d9;
    --card-brown: #3a2c2b;
    --pattern-brown: #46373a;
    --band-pink: #d6157f;
    --band-edge: #f06aaf;
    --label-white: #ffffff;
    --peach: #eaa48f;
    --peach-soft: #f0b9a8;
    --ink-brown: #3a2c2b;
    --gold: #c9a13b;
    --text-light: #f3ebe8;
  }
  * { margin: 0; padding: 0; box-sizing: border-box; }
  html, body { width: 1200px; height: 852px; overflow: hidden; }
  body {
    background: var(--backdrop);
    font-family: "Open Sans", sans-serif;
    position: relative;
  }
  .card {
    position: absolute;
    top: 276px;
    width: 525px;
    height: 300px;
    border-radius: 22px;
    overflow: hidden;
    box-shadow: 0 4px 14px rgba(0,0,0,0.18);
  }
  .card-front { left: 50px; }
  .card-back { left: 625px; }
  .damask-field {
    position: absolute; inset: 0;
    background: radial-gradient(circle at 50% 50%, var(--pattern-brown), var(--card-brown) 80%);
  }

  /* front */
  .ribbon-band {
    position: absolute; left: 0; right: 0; top: 128px; height: 44px;
    background: var(--band-pink);
    border-top: 2px solid var(--band-edge);
    border-bottom: 2px solid var(--band-edge);
  }
  .name-panel {
    position: absolute; left: 132px; top: 90px; width: 261px; height: 120px;
    background: var(--label-white);
    border-radius: 18px;
    box-shadow: 0 2px 8px rgba(0,0,0,0.3);
    display: flex; align-items: center; justify-content: center;
  }
  .brand-name {
    font-family: "Open Sans", sans-serif;
    font-weight: 600;
    font-size: 30px;
    line-height: 1;
    letter-spacing: 1px;
    color: var(--ink-brown);
    white-space: nowrap;
  }

  /* back */
  .back-name {
    position: absolute; left: 40px; top: 130px; width: 210px;
    display: flex; justify-content: center;
  }
  .back-name .brand-name { color: var(--peach-soft); font-size: 26px; }
  .gold-stroke { position: absolute; left: 262px; top: 40px; }
  .owner-block { position: absolute; left: 300px; top: 50px; }
  .owner-title { font-size: 14px; color: var(--text-light); }
  .owner-name { font-family: "Great Vibes", cursive; font-size: 30px; color: var(--text-light); line-height: 1.1; }
  .contact-list { list-style: none; position: absolute; left: 300px; top: 160px; }
  .contact-list li {
    display: flex; align-items: center; gap: 9px;
    font-size: 12.5px; color: var(--peach-soft); line-height: 19px;
    white-space: nowrap;
  }
  .contact-icon { width: 11px; height: 11px; flex: none; }
</style>
</head>
<body>

<section class="card card-front" aria-label="Business card front">
  <div class="damask-field" role="img" aria-label="Brown damask pattern background"></div>
  <div class="ribbon-band"></div>
  <div class="name-panel">
    <span class="brand-name">Sugar Loom</span>
  </div>
</section>

<section class="card card-back" aria-label="Business card back">
  <div class="damask-field" role="img" aria-label="Brown damask pattern background"></div>
  <div class="back-name">
    <span class="brand-name">Sugar Loom</span>
  </div>
  <svg class="gold-stroke" width="20" height="220" viewBox="0 0 20 220" aria-hidden="true">
    <path d="M1 0 Q11 110 19 220 Q7 110 1 0Z" fill="var(--gold)"/>
  </svg>
  <div class="owner-block">
    <p class="owner-title">Sugar Loom by</p>
    <p class="owner-name">Dana Welch</p>
  </div>
  <ul class="contact-list">
    <li><svg class="contact-icon" viewBox="0 0 12 12"><path d="M2 1h3l1 3-2 1a6 6 0 0 0 3 3l1-2 3 1v3c-6 0-10-4-10-9z" fill="var(--peach)"/></svg>(516) 555-0147</li>
    <li><svg class="contact-icon" viewBox="0 0 12 12"><rect x="0.5" y="2" width="11" height="8" fill="var(--peach)"/><path d="M0.5 2l5.5 4 5.5-4" stroke="var(--card-brown)" fill="none"/></svg>hello@sugarloom.com</li>
    <li><svg class="contact-icon" viewBox="0 0 12 12"><circle cx="6" cy="6" r="5.5" fill="var(--peach)"/><path d="M0.5 6h11M6 0.5c-3 3-3 8 0 11M6 0.5c3 3 3 8 0 11" stroke="var(--card-brown)" fill="none" stroke-width="0.8"/></svg>www.sugarloomsweets.com</li>
    <li><svg class="contact-icon" viewBox="0 0 12 12"><rect width="12" height="12" rx="2" fill="var(--peach)"/></svg>sugarloomnyc</li>
    <li><svg class="contact-icon" viewBox="0 0 12 12"><rect width="12" height="12" rx="2" fill="var(--peach)"/></svg>sugarloom_ny</li>
  </ul>
</section>

</body>
</html>
```